Music Producer Website

I need a website designed for my music production company. We specialize in finding talented musicians and matching them with music producers all over the United States. A visitor can create a profile and/or upload their music demo and we submit it to thousands of music producers and production companies for review. In many cases, our members will receive multiple signing offers from music producers allowing them to choose the contract that is best for them. "We turn aspiring musicians into SuperStars!"
Please include photos that reflect all genres of music (black artists, white artists, both male and female.) We produce all types of music including rap, R&B, rock, country, and Hip Hop.
When a user creates a profile, they become visible to thousands of record producers who are looking to sign new talent and make them stars.
Somewhere in the top half of the page, please include a small form that the visitor can fill out. The form should look as follows:
Title (large and bold): Contact Us or Submit Music Demo
Fields to include (* = required): First Name*, Last Name*, Age, Zip Code, Email Address*, Daytime Phone, Evening Phone, Comments
Then, there will be a "submit" button to proceed to next step of form. Just below the "submit" button, should be the following verbiage: "After submitting, you will have the opportunity to upload demos of your music (optional) and provide other pertinent information about yourself, band, or group."
Updates
Reason: I have not seen a design that I am 100% satisfied with yet. Ideally, rotating header images (GIF or other) with several different music producers in studio (male, female, black, white) would be perfect. Here are some examples of how the header pics could look:
http://files.quillmarsh.net/art_img/514302/806421/806421_7391046_514302_image.jpg
http://files.quillmarsh.net/art_img/514302/806421/806421_7391058_514302_image.jpg
http://files.quillmarsh.net/art_img/514302/806421/806421_7391037_514302_image.jpg
Also, there should be a form on the site (somewhere in upper half of the page) with the following headline:
GET FOUND AND BECOME A STAR! (super large, super-bold font)
Contact Us or Submit Your Music for Review (large font, not as bold as headline)
First Name
Last Name
Age
Zip Code
Email Address
Daytime Phone
Evening Phone
Comments
Target Market(s)
We are targeting all types of musicians including rock, rap, pop, R&B, country, gospel, etc.
Industry/Entity Type
Artists
Colors
Designer to choose colors to be used in the design.
Look and feel
Each slider illustrates characteristics of the customer's brand and the style your logo design should communicate.

```html
<!DOCTYPE html>
<html lang="en">
<head>
<meta charset="utf-8">
<title>Cadenza Music Productions</title>
<link rel="stylesheet" href="https://fonts.googleapis.com/css2?family=Lato:wght@300;400;700;900&display=swap">
<style>
:root{
  --black:#000;
  --ink:#0b0b0b;
  --gold:#b9a57a;
  --gold-soft:#a8976f;
  --white:#fff;
  --field:#f4f4f4;
  --field-text:#9a9a9a;
  --beige:#e9e0d6;
  --red:#c0392b;
  --grey:#9b9b9b;
}
*{box-sizing:border-box;margin:0;padding:0}
html,body{width:1200px;height:2261px;overflow:hidden;background:var(--black)}
body{position:relative;font-family:'Lato',sans-serif;color:var(--white)}
.abs{position:absolute}

/* hero */
.hero-photo{left:0;top:0;width:1200px;height:942px;
  background:radial-gradient(ellipse at 55% 35%,#3b5bd6 0%,#1c2d8a 30%,#0b1240 60%,#05060f 100%)}
.header-bar{left:119px;top:0;width:958px;height:122px;background:rgba(0,0,0,.82)}
.brand{left:150px;top:34px;text-align:center;color:var(--gold);font-weight:700;letter-spacing:3px;line-height:1}
.brand .name{font-size:40px}
.brand .sub{font-size:13px;letter-spacing:2px;margin-top:6px}
.account{left:772px;top:25px;font-size:15px;color:var(--white)}
.social{top:21px;width:28px;height:28px;border-radius:50%;background:#555}
.search{left:1030px;top:21px;width:30px;height:30px;border-radius:50%;background:var(--gold-soft)}
.nav{top:82px;font-size:16px;font-weight:700;color:var(--white)}
.nav span{color:var(--gold)}
.nav-active{left:505px;top:66px;width:98px;height:3px;background:var(--gold)}
.arrow{top:276px;width:24px;height:32px}
.tag-line{left:697px;top:335px;width:371px;height:38px;background:#e9e9e9;color:#111;font-size:24px;font-weight:700;text-align:center;line-height:38px}
.tag-big{left:550px;top:377px;width:524px;height:90px;background:rgba(0,0,0,.8);font-size:68px;font-weight:700;text-align:right;padding-right:16px;line-height:90px}

/* form */
.form-panel{left:75px;top:537px;width:1061px;height:405px;background:rgba(0,0,0,.86)}
.form-title{left:122px;top:556px;line-height:1}
.form-title .l1{font-size:41px;font-weight:700}
.form-title .l2{font-size:70px;font-weight:700;color:var(--gold);margin-top:2px}
.field{height:29px;background:var(--field);color:var(--field-text);font-size:15px;padding:5px 10px;line-height:19px}
.req{color:#ddd;font-size:11px}
.artist-photo{left:763px;top:565px;width:300px;height:264px;
  background:radial-gradient(ellipse at 50% 45%,#8a8a8a 0%,#3a3a3a 45%,#000 80%)}
.submit{left:772px;top:836px;width:306px;height:44px;background:var(--gold);font-size:30px;font-weight:700;text-align:center;line-height:44px}
.form-note{left:75px;top:896px;width:1061px;text-align:center;font-size:12.5px;color:var(--gold-soft)}

/* welcome */
.welcome{left:0;top:942px;width:1200px;height:377px;
  background:linear-gradient(90deg,#1f140b 0%,#4a3520 45%,#2d1f12 70%,#120c07 100%)}
.welcome-title{left:160px;top:1035px;font-size:68px;font-weight:700;line-height:1.15}
.welcome-title .gold{color:var(--gold)}
.welcome-copy{left:527px;top:1008px;width:553px;font-size:13px;line-height:17px;color:#eee}
.welcome-copy p+p{margin-top:17px}

/* quote */
.quote-rule{left:122px;top:1407px;width:955px;height:1px;background:#555}
.quote-badge{left:558px;top:1364px;width:84px;height:84px}
.quote-text{left:122px;top:1452px;width:955px;text-align:center;font-size:22px;font-weight:300;line-height:31px;color:#c9bb97}
.quote-author{left:0;top:1546px;width:1200px;text-align:center;font-size:15px;font-weight:700}
.quote-author span{color:var(--gold)}
.dot{width:10px;height:10px;border-radius:50%;background:var(--gold)}
.dot.on{background:var(--red)}

/* concerts */
.strip{left:0;top:1620px;width:119px;height:468px;background:var(--beige)}
.concert-col{left:119px;top:1620px;width:390px;height:468px;background:var(--black)}
.concert-title{left:119px;top:1626px;width:390px;text-align:center;line-height:1}
.concert-title .l1{font-size:62px;font-weight:700}
.concert-title .l2{font-size:58px;font-weight:700;color:var(--gold)}
.next-bar{left:119px;top:1756px;width:390px;height:64px;background:var(--gold)}
.next-bar .label{position:absolute;left:28px;top:18px;font-size:26px;font-weight:700}
.gig-date{left:150px;font-size:17px;font-weight:700}
.gig-venue{left:150px;width:340px;font-size:19px;font-weight:700;line-height:25px;color:var(--gold)}
.gig-rule{left:140px;top:1965px;width:355px;height:1px;background:#444}
.map{left:509px;top:1620px;width:691px;height:468px;
  background:linear-gradient(135deg,#e4d8c4 0%,#c9a98a 35%,#e8dfd0 60%,#b48d6a 100%)}
.pin{width:30px;height:38px;background:#222;border:1px solid #666;color:#fff;font-size:10px;font-weight:700;text-align:center;line-height:11px;padding-top:3px}

/* footer */
.footer-brand{left:0;top:2118px;width:1200px;text-align:center;color:var(--gold);font-weight:700;letter-spacing:3px;line-height:1}
.footer-brand .name{font-size:34px}
.footer-brand .sub{font-size:11px;margin-top:4px}
.copyright{left:0;top:2195px;width:1200px;text-align:center;font-size:12px}
.footer-links{left:0;top:2221px;width:1200px;text-align:center;font-size:12px}
</style>
</head>
<body>

<!-- hero -->
<div class="abs hero-photo" role="img" aria-label="Rock guitarist performing on a concert stage in front of a large crowd under blue stage lights"></div>
<div class="abs header-bar"></div>
<div class="abs brand"><div class="name">CADENZA</div><div class="sub">MUSIC PRODUCTIONS</div></div>
<div class="abs account">login / register</div>
<div class="abs social" style="left:911px"></div>
<div class="abs social" style="left:944px"></div>
<div class="abs social" style="left:977px"></div>
<svg class="abs search" viewBox="0 0 30 30" aria-label="Search"><circle cx="15" cy="15" r="15" fill="#a8976f"/><circle cx="13.5" cy="13.5" r="5" fill="none" stroke="#fff" stroke-width="2"/><line x1="17" y1="17" x2="21" y2="21" stroke="#fff" stroke-width="2"/></svg>
<div class="abs nav-active"></div>
<div class="abs nav" style="left:505px">About <span>Cadenza</span></div>
<div class="abs nav" style="left:657px">Team <span>Cadenza</span></div>
<div class="abs nav" style="left:802px">Join <span>Cadenza</span></div>
<div class="abs nav" style="left:932px">Contact <span>Cadenza</span></div>
<svg class="abs arrow" style="left:36px" viewBox="0 0 24 32"><polyline points="17,6 7,16 17,26" fill="none" stroke="#fff" stroke-width="4"/></svg>
<svg class="abs arrow" style="left:1138px" viewBox="0 0 24 32"><polyline points="7,6 17,16 7,26" fill="none" stroke="#fff" stroke-width="4"/></svg>
<div class="abs tag-line">We turn aspiring musicians into</div>
<div class="abs tag-big">SuperStars!</div>

<!-- form -->
<div class="abs form-panel"></div>
<div class="abs form-title"><div class="l1">GET FOUND AND</div><div class="l2">BECOME A STAR!</div></div>
<div class="abs field" style="left:120px;top:674px;width:308px">First name</div>
<div class="abs req" style="left:430px;top:660px">*</div>
<div class="abs field" style="left:447px;top:674px;width:305px">Last name</div>
<div class="abs req" style="left:754px;top:660px">*</div>
<div class="abs field" style="left:120px;top:720px;width:142px">Age</div>
<div class="abs field" style="left:284px;top:720px;width:144px">Zip Code</div>
<div class="abs field" style="left:447px;top:720px;width:305px">Email Address</div>
<div class="abs req" style="left:754px;top:706px">*</div>
<div class="abs field" style="left:120px;top:763px;width:308px">Daytime Phone</div>
<div class="abs field" style="left:447px;top:763px;width:305px">Evening Phone</div>
<div class="abs field" style="left:120px;top:804px;width:632px;height:76px">Comments</div>
<div class="abs artist-photo" role="img" aria-label="Black and white portrait of a young artist wearing headphones and sunglasses"></div>
<div class="abs submit">SUBMIT</div>
<div class="abs form-note">After submitting, you will have the opportunity to upload demos of your music (optional) and provide other pertinent information about yourself, band, or group.</div>

<!-- welcome -->
<div class="abs welcome" role="img" aria-label="Guitarist silhouetted on a warmly lit stage"></div>
<div class="abs welcome-title">Welcome<br><span class="gold">to Cadenza</span></div>
<div class="abs welcome-copy">
<p>Lorem ipsum dolor sit amet, consectetur adipiscing elit. Sed adipiscing sit amet sem sit amet viverra. Cras porta justo risus, quis sodales diam placerat vitae. Quisque eget dui orci. Cras aliquet, odio quis gravida fermentum, nibh lorem vulputate nunc, ut condimentum mauris ipsum non ipsum. Duis eleifend mauris nibh, ac hendrerit nisi bibendum dignissim. Nullam blandit urna vulputate nisl dignissim, vel tempus ante porttitor. Sed sed mi ac eros viverra rhoncus. Sed tempor sodales libero sit amet convallis.</p>
<p>Morbi ac lectus lectus. Proin vitae facilisis enim. Suspendisse a fermentum magna. Curabitur accumsan ac magna ac vehicula. Sed sollicitudin, magna sed commodo pretium, arcu nunc tincidunt sem, quis laoreet felis eros et arcu. Maecenas porta tempus vulputate. Sed iaculis orci adipiscing lectus molestie dapibus. In vehicula, libero sit amet dapibus luctus, felis massa tincidunt eros, sodales fringilla lorem sem nec diam.</p>
</div>

<!-- testimonial -->
<div class="abs quote-rule"></div>
<svg class="abs quote-badge" viewBox="0 0 84 84"><path d="M2 43 A40 40 0 0 1 82 43" fill="#000" stroke="#555" stroke-width="1.5"/><rect x="0" y="43" width="84" height="41" fill="#000"/><text x="42" y="62" text-anchor="middle" font-family="Lato,sans-serif" font-weight="900" font-size="44" fill="#fff">“</text></svg>
<div class="abs quote-text">" Lorem ipsum dolor sit amet, consectetur adipiscing elit. In imperdiet diam augue,<br>vitae lacinia leo lacinia sit amet. Nulla facilisi. Cras cursus sed odio a mollis"</div>
<div class="abs quote-author">Dana Hollis &nbsp;<span>producers</span></div>
<div class="abs dot on" style="left:567px;top:1595px"></div>
<div class="abs dot" style="left:585px;top:1595px"></div>
<div class="abs dot" style="left:603px;top:1595px"></div>

<!-- concerts -->
<div class="abs strip"></div>
<div class="abs concert-col"></div>
<div class="abs concert-title"><div class="l1">Concert</div><div class="l2">schedule</div></div>
<div class="abs next-bar"><span class="label">NEXT CONCERT</span>
<svg style="position:absolute;left:332px;top:14px" width="38" height="36" viewBox="0 0 38 36"><rect x="1" y="4" width="36" height="31" fill="none" stroke="#fff" stroke-width="2"/><rect x="1" y="4" width="36" height="7" fill="#fff"/><g fill="#fff"><rect x="6" y="15" width="5" height="4"/><rect x="14" y="15" width="5" height="4"/><rect x="22" y="15" width="5" height="4"/><rect x="30" y="15" width="4" height="4"/><rect x="6" y="22" width="5" height="4"/><rect x="14" y="22" width="5" height="4"/><rect x="22" y="22" width="5" height="4"/><rect x="30" y="22" width="4" height="4"/><rect x="6" y="29" width="5" height="3"/><rect x="14" y="29" width="5" height="3"/></g><rect x="9" y="0" width="3" height="7" fill="#fff"/><rect x="26" y="0" width="3" height="7" fill="#fff"/></svg>
</div>
<div class="abs dot on" style="left:295px;top:1838px"></div>
<div class="abs dot" style="left:313px;top:1838px"></div>
<div class="abs dot" style="left:331px;top:1838px"></div>
<div class="abs gig-date" style="top:1865px">2 November 2013</div>
<div class="abs gig-venue" style="top:1898px">Harbor Arena - 2200 W Harbor Ave, Los Angeles, CA, US</div>
<div class="abs gig-rule"></div>
<div class="abs gig-date" style="top:1986px">10 November 2013</div>
<div class="abs gig-venue" style="top:2021px">Harbor Arena - 2200 W Harbor Ave, Los Angeles, CA, US</div>
<div class="abs map" role="img" aria-label="Map of the south-western United States marking upcoming concert locations"></div>
<div class="abs pin" style="left:708px;top:1775px">10<br>Nov<br><span style="font-size:7px">2013</span></div>
<div class="abs pin" style="left:600px;top:1866px">2<br>Nov<br><span style="font-size:7px">2013</span></div>

<!-- footer -->
<div class="abs footer-brand"><div class="name">CADENZA</div><div class="sub">MUSIC PRODUCTIONS</div></div>
<div class="abs copyright">Copyright 2013 © Music Producers. Power by Brightwell</div>
<div class="abs footer-links">Privacy Policy | Terms and Conditions | Site Map | Feedback | Report Bug | Contact Us</div>

</body>
</html>
```